KRL Stationery Design Project

Dear Designers,
We need a new stationery design for company to match our new logo.
Designers should provide a design for the following:
1. Business Card: 3.5x2 Inches.
2. Letterhead: A4 size.
3. Envelops: 25x35.5 Cm.
You can keep the Arabic name at the bottom of the logo Or you can use the separate attached Arabic Name.
Please refer to the attached logo guide for design information.
Sample Business Card information:
Name: Tarek Sowan
Position: Operation Manager
Tel: +966 920007164 Ex. 500
Fax: +966 (3)8842617
Mob: +966 (5)00263817
email: tarek@krl-example.com.sa
URL: www.krl-example.com.sa
Address:
Nakheel Heights, Suite 718
Zayed bin Omar Str.
Khobar, 31847
Saudi Arabia
Updates
Dear All,
Please note, we had uploaded our logo along with Arabic writing in Adobe illustrator format (.ai).
Regards,
Karim
Dear All,
A sample data for the business card had been added as per your request.
Regards,
Karim

```html
<!DOCTYPE html>
<html lang="en">
<head>
<meta charset="utf-8">
<title>KRL Tracking – Business Card</title>
<link href="https://fonts.googleapis.com/css2?family=Cinzel:wght@400;700&family=Open+Sans:wght@400&display=swap" rel="stylesheet">
<style>
  :root {
    --backdrop: #232323;
    --card: #ffffff;
    --navy: #0d2d57;
    --grey: #9a9a9a;
    --grey-light: #c9c9c9;
    --ink: #3a3a3a;
  }
  * { margin: 0; padding: 0; box-sizing: border-box; }
  html, body { width: 1200px; height: 472px; overflow: hidden; background: var(--backdrop); }
  .canvas { position: relative; width: 1200px; height: 472px; background: var(--backdrop); }

  .card {
    position: absolute;
    width: 525px; height: 299px;
    background: var(--card);
    border-radius: 14px;
    overflow: hidden;
  }
  .card--front { left: 38px; top: 87px; }
  .card--back { left: 627px; top: 77px; }

  .brand {
    position: absolute;
    display: flex; align-items: center; gap: 10px;
    font-family: "Cinzel", serif;
    font-weight: 700;
    color: var(--navy);
    white-space: nowrap;
  }
  .brand__dot { width: 16px; height: 16px; border-radius: 50%; background: var(--navy); }
  .card--front .brand { left: 0; right: 0; justify-content: center; top: 52px; font-size: 40px; }
  .card--back .brand { left: 0; right: 0; justify-content: center; top: 105px; font-size: 40px; }

  .person {
    position: absolute; right: 298px; top: 166px;
    text-align: right; font-family: "Cinzel", serif;
  }
  .person__name { font-size: 18px; font-weight: 700; color: var(--navy); letter-spacing: 0.5px; }
  .person__title { font-size: 12px; color: var(--grey); margin-top: 2px; letter-spacing: 1px; }

  .divider {
    position: absolute; left: 252px; top: 156px;
    width: 2px; height: 64px;
    background: linear-gradient(to bottom, transparent, var(--grey-light), transparent);
  }

  .contacts {
    position: absolute; left: 261px; top: 154px;
    list-style: none; font-family: "Cinzel", serif;
    font-size: 13px; color: var(--ink); line-height: 17px;
  }
  .contacts li { display: flex; align-items: center; gap: 6px; }
  .contacts svg { width: 10px; height: 10px; fill: var(--navy); flex: none; }

  .footer-band { position: absolute; left: 0; bottom: 0; width: 525px; height: 80px; }
  .address {
    position: absolute; left: 30px; bottom: 16px;
    font-family: "Cinzel", serif; font-size: 14px; color: #fff; letter-spacing: 0.3px;
  }

  .website {
    position: absolute; left: 0; right: 0; top: 240px; text-align: center;
    font-family: "Open Sans", sans-serif; font-size: 12px; color: var(--ink); letter-spacing: 0.5px;
  }
</style>
</head>
<body>
<div class="canvas">

  <section class="card card--front">
    <div class="brand"><span class="brand__dot"></span>KRL Tracking</div>

    <div class="person">
      <p class="person__name">YOUR NAME</p>
      <p class="person__title">TITLE</p>
    </div>

    <div class="divider"></div>

    <ul class="contacts">
      <li><svg viewBox="0 0 10 10"><path d="M2 0.5 L4 2.5 L3 3.8 Q4.3 6 6.2 7 L7.5 6 L9.5 8 L8 9.5 Q2 9 0.5 2 Z"/></svg>123-456-7890</li>
      <li><svg viewBox="0 0 10 10"><path d="M1.5 4 L2.8 1 H7.2 L8.5 4 H9.5 V8 H8.3 V9.3 H6.8 V8 H3.2 V9.3 H1.7 V8 H0.5 V4 Z"/></svg>123-456-7890</li>
      <li><svg viewBox="0 0 10 10"><path d="M0.5 2 H9.5 V8.5 H0.5 Z M1.2 2.6 L5 5.6 L8.8 2.6 Z" fill-rule="evenodd"/></svg>INFO@MAILBOX.COM</li>
      <li><svg viewBox="0 0 10 10"><circle cx="5" cy="5" r="4.5"/></svg>WWW.WEBSITE.COM</li>
    </ul>

    <svg class="footer-band" viewBox="0 0 525 80" preserveAspectRatio="none" aria-hidden="true">
      <path d="M0 26 Q220 -6 525 44 L525 34 Q220 -16 0 18 Z" fill="var(--grey-light)"/>
      <path d="M0 32 Q220 4 525 52 L525 80 L0 80 Z" fill="var(--navy)"/>
    </svg>
    <p class="address">Street Name, City Name, State, City Zip Code</p>
  </section>

  <section class="card card--back">
    <div class="brand"><span class="brand__dot"></span>KRL Tracking</div>
    <p class="website">www.website.com</p>
  </section>

</div>
</body>
</html>
```